Business Card for a mobile physiotherapy company

I need a layout for a business card for a mobile physiotherapy company.
Slogan is "Mobile Physiotherapy - Your Road To Recovery"
Phone number is 867-555-0142
Email VardenTherapy@postnest.ca (subject to change with website)
Website www.VardenTherapy.ca
My name and credentials: Luke Varden Luke Varden, BSc(kin), MPT, CAFCI, IMS
Information maybe included: Direct Billing, Services including Physiotherapy, IMS, acupuncture
Maybe include facebook and instagram logos
One side with the logo clean and sharp
Other side with details, try not to look too busy, keep everything concise

```html
<!DOCTYPE html>
<html lang="en">
<head>
<meta charset="utf-8">
<title>Varden Therapy – Business Card</title>
<link href="https://fonts.googleapis.com/css2?family=Lato:wght@400;700&family=Roboto:wght@400&display=swap" rel="stylesheet">
<style>
  :root {
    --navy: #2b4a78;
    --navy-deep: #264470;
    --green: #1d5f4f;
    --paper: #ffffff;
    --backdrop: #b9b9b9;
    --rule: #2b4a78;
  }
  html, body {
    margin: 0;
    width: 1200px;
    height: 930px;
    overflow: hidden;
    background: var(--backdrop);
    font-family: "Lato", sans-serif;
  }
  .stage {
    width: 1200px;
    height: 930px;
    display: flex;
    flex-direction: column;
    align-items: center;
    justify-content: center;
    gap: 50px;
  }
  .card {
    position: relative;
    width: 700px;
    height: 400px;
    border-radius: 26px;
    overflow: hidden;
    box-shadow: 0 6px 18px rgba(0,0,0,0.22);
  }

  /* Front */
  .card--front {
    background: var(--navy);
    color: var(--paper);
  }
  .front-brand {
    position: absolute;
    top: 130px;
    left: 0;
    right: 0;
    display: flex;
    align-items: center;
    justify-content: center;
    gap: 14px;
  }
  .brand-mark {
    width: 22px;
    height: 22px;
    background: currentColor;
  }
  .brand-name {
    font-family: "Lato", sans-serif;
    font-weight: 700;
    font-size: 46px;
    letter-spacing: 3px;
    text-transform: uppercase;
  }
  .front-slogan {
    position: absolute;
    bottom: 56px;
    left: 0;
    right: 0;
    text-align: center;
    font-size: 19px;
    letter-spacing: 0.3px;
  }

  /* Back */
  .card--back {
    background: var(--paper);
  }
  .back-brand {
    position: absolute;
    top: 140px;
    left: 40px;
    display: flex;
    align-items: center;
    gap: 10px;
    color: var(--navy);
  }
  .back-brand .brand-name { font-size: 30px; letter-spacing: 2px; }
  .back-brand .brand-mark { width: 16px; height: 16px; }

  .holder {
    position: absolute;
    top: 40px;
    right: 44px;
    text-align: right;
  }
  .holder-name {
    font-family: "Roboto", sans-serif;
    font-size: 30px;
    line-height: 1.1;
    color: var(--navy);
    margin: 0;
  }
  .holder-services {
    margin: 10px 0 0;
    font-size: 17px;
    line-height: 1.35;
    color: var(--green);
  }
  .rule {
    position: absolute;
    height: 2px;
    background: var(--rule);
  }
  .rule--services { top: 178px; right: 44px; width: 300px; }
  .rule--contact { top: 262px; left: 40px; width: 330px; }

  .contact {
    position: absolute;
    left: 40px;
    top: 276px;
    list-style: none;
    margin: 0;
    padding: 0;
    font-size: 18px;
    color: var(--green);
  }
  .contact li {
    display: flex;
    align-items: center;
    gap: 12px;
    height: 30px;
  }
  .contact svg { width: 14px; height: 14px; fill: none; stroke: var(--navy); stroke-width: 1.6; }
  .wave {
    position: absolute;
    left: 0;
    bottom: 0;
    width: 700px;
    height: 200px;
  }
</style>
</head>
<body>
<main class="stage">
  <section class="card card--front" aria-label="Card front">
    <div class="front-brand">
      <span class="brand-mark"></span>
      <span class="brand-name">Varden Therapy</span>
    </div>
    <p class="front-slogan">Mobile Physiotherapy - Your Road To Recovery</p>
  </section>

  <section class="card card--back" aria-label="Card back">
    <svg class="wave" viewBox="0 0 700 200" preserveAspectRatio="none" aria-hidden="true">
      <path d="M700 30 C560 40 500 150 300 190 C230 200 180 198 150 200 L700 200 Z" fill="var(--navy-deep)"/>
      <path d="M700 18 C560 28 490 140 290 182 C230 194 180 194 140 196" fill="none" stroke="var(--green)" stroke-width="4"/>
    </svg>

    <div class="back-brand">
      <span class="brand-mark"></span>
      <span class="brand-name">Varden Therapy</span>
    </div>

    <div class="holder">
      <h1 class="holder-name">Luke Varden, BSc(kin),<br>MPT, CAFCI, IMS</h1>
      <p class="holder-services">Direct Billing, Services including<br>Physiotherapy, IMS, acupuncture</p>
    </div>
    <div class="rule rule--services"></div>
    <div class="rule rule--contact"></div>

    <ul class="contact">
      <li>
        <svg viewBox="0 0 16 16"><path d="M4 1.5 L6.5 4.5 L5 6.5 C6 8.5 7.5 10 9.5 11 L11.5 9.5 L14.5 12 L12.5 14.5 C7 14 2 9 1.5 3.5 Z"/></svg>
        867-555-0142
      </li>
      <li>
        <svg viewBox="0 0 16 16"><rect x="1.5" y="3.5" width="13" height="9"/><path d="M1.5 3.5 L8 9 L14.5 3.5"/></svg>
        VardenTherapy@postnest.ca
      </li>
      <li>
        <svg viewBox="0 0 16 16"><circle cx="8" cy="8" r="6.5"/><path d="M1.5 8 H14.5 M8 1.5 C5 5 5 11 8 14.5 M8 1.5 C11 5 11 11 8 14.5"/></svg>
        www.VardenTherapy.ca
      </li>
    </ul>
  </section>
</main>
</body>
</html>
```